Maple Beacon Website

We are starting a marketing company and to do that we need a website! We want a website that will inspire and persuade to bring out the awesomeness in our clients.
What we want to see:
- Inspirational and persuasive imagery that relate to Branding.
- No cliche images eg. business man, suits and hand shakes
- We want to transform and educate our clients.
- We want to show them the path and would like our website to really act as a guide that guides them step by step through our process.
- We want the portray that we are an investment but not have a pretentious way to it. We put our heart into every project and that is how we treat our clients.
-When you submit your design please include what platform you have created for. Preference would be Wordpress or Joobla.

We have included the psd file for the wire frame, logo files, font files, site map and a link to a video we create to give you more information on what we would like to see. http://clipvault.example/t/qk82LmZpr

Feel free to make small modification to the logos if you think it will improve it. Your creativity and advice is most welcome.
Updates

One thing we forgot. We would like to have our contact information near the top of the website as well as at the bottom.  Here is out contact info:

Email: info@maplebeacon.example
Phone: 587-555-0142

Project Deadline Extended
Reason: As we are new with the platform and that we want to optimize our results, we decided to extend the deadline by 15 days. Thanks!

Target Market(s)

28-60, Male and Female, Oil field, Local Businesses, Dentists, Chiropractors, Hair salon, Construction/Renovation, Events etc

Industry/Entity Type

Investment

Requirements
Must have
• - 4 Inspirational and persuasive Imagery for the top portion of the website
- Must have a feel as if your not on a website an example of this is linked below.
http://www.artbidhub.example/design/402957/web-design-by-lena-torvik
Nice to have
• - Creative advice from you.
- Creative buttons for Get Free Quote and Subscribe buttons. Something out of the box that draws peoples attention. eg. a 'B' button. Just and example but still something related to branding.
Should not have
• No Cliches

```html
<!DOCTYPE html>
<html lang="en">
<head>
<meta charset="utf-8">
<title>Maple Beacon</title>
<link href="https://fonts.googleapis.com/css2?family=Open+Sans:wght@400;600;700&family=Signika:wght@600;700&display=swap" rel="stylesheet">
<style>
:root{
  --green:#6aa72a;
  --green-dark:#4b7d1c;
  --green-light:#8cc63f;
  --lime:#9ccc3c;
  --page:#f7f7f7;
  --text:#666;
  --dark:#333;
  --grey:#9a9a9a;
  --line:#d4d4d4;
}
*{margin:0;padding:0;box-sizing:border-box}
html,body{width:1200px;height:1063px;overflow:hidden}
body{position:relative;background:var(--page);font-family:"Open Sans",sans-serif;color:var(--text)}
.top-band{position:absolute;left:0;top:0;width:1200px;height:146px;
  background:linear-gradient(#8cc63f,#6aa72a)}
.contact{position:absolute;right:175px;font-size:16px;color:#fff;display:flex;align-items:center;gap:6px}
.contact .phone{font-weight:700}
.contact svg{display:block}
.contact-top{top:16px}
.frame{position:absolute;left:170px;top:50px;width:857px;height:339px;background:#fff;border:1px solid #ccc;overflow:hidden}
.sidebar{position:absolute;left:0;top:0;width:205px;height:339px;background:#efefef;border-right:1px solid #d8d8d8}
.brand{height:96px;display:flex;flex-direction:column;align-items:center;justify-content:center;gap:6px;
  background:linear-gradient(#fafafa,#e9e9e9)}
.brand-name{display:flex;align-items:center;gap:7px;font-family:"Signika",sans-serif;font-weight:700;font-size:23px;color:var(--green)}
.brand-name i{width:12px;height:12px;border-radius:50%;background:var(--green)}
.tagline{font-size:11px;font-style:italic;color:#555}
.nav{list-style:none}
.nav li{height:33.5px;border-top:1px solid #d8d8d8;padding-left:14px;display:flex;align-items:center;
  font-size:14px;font-weight:700;color:var(--green-dark)}
.connect{position:absolute;left:0;bottom:0;width:205px;height:66px;background:linear-gradient(#8a8a8a,#a9a9a9);
  display:flex;align-items:center;justify-content:space-between;padding:0 25px 0 16px}
.connect span{font-family:"Signika",sans-serif;font-weight:700;font-size:19px;line-height:18px;color:#fff}
.connect b{width:40px;height:40px;border-radius:3px;background:linear-gradient(#8cc63f,#5c9a22);border:1px solid #4b7d1c;
  display:flex;align-items:center;justify-content:center}
.hero{position:absolute;left:205px;top:0;width:652px;height:273px;
  background:radial-gradient(circle at 55% 45%,#c7e39a 0,#f1f1f1 25%,#b4b4b4 75%,#d9d9d9 100%)}
.tabs{position:absolute;left:205px;top:273px;width:652px;height:66px;display:flex;background:linear-gradient(#5a8f26,#4a7a1d)}
.tab{flex:1;position:relative;display:flex;align-items:center;justify-content:center;border-left:1px solid #8cc63f;
  font-family:"Signika",sans-serif;font-weight:700;font-size:15px;color:#e6e6e6}
.tab:first-child{border-left:none;color:#fff}
.tab::before{content:"";position:absolute;top:-8px;left:50%;margin-left:-8px;width:16px;height:16px;border-radius:50%;
  background:radial-gradient(circle at 40% 35%,#ccc,#666);border:1.5px solid #fff}
.tab:first-child::before{background:radial-gradient(circle at 40% 35%,#b9e46a,#5c9a22)}
.tab:first-child{padding-right:28px}
.social{position:absolute;left:171px;top:403px;display:flex;gap:7px}
.social span{width:46px;height:45px;border-radius:2px;background:linear-gradient(#5b5b5b,#2f2f2f)}
.tips{position:absolute;left:389px;top:409px;line-height:16px}
.tips strong{display:block;font-family:"Signika",sans-serif;font-size:19px;color:var(--lime)}
.tips small{font-size:14px;font-weight:600;color:#555}
.email-input{position:absolute;left:590px;top:409px;width:202px;height:36px;border:1px solid #ccc;border-radius:2px;
  background:#fff;font-size:12px;color:#666;padding:9px 7px}
.btn{position:absolute;top:409px;height:36px;border-radius:2px;color:#fff;font-family:"Signika",sans-serif;font-weight:600;
  font-size:15px;display:flex;align-items:center;justify-content:center}
.btn-subscribe{left:797px;width:82px;background:linear-gradient(#b8b8b8,#8f8f8f);border:1px solid #888}
.btn-quote{left:885px;width:140px;background:linear-gradient(#8cc63f,#5c9a22);border:1px solid #4b7d1c}
.rule{position:absolute;left:175px;top:461px;width:848px;border-top:1px dashed #aaa}
.content{position:absolute;left:175px;top:485px;width:850px;font-size:14px;line-height:19px}
.content h1{font-family:"Signika",sans-serif;font-weight:700;font-size:22px;color:var(--dark);margin-left:-3px;margin-bottom:16px}
.content h2{font-size:14px;font-weight:700;color:var(--green-dark);margin-top:19px}
.checks{list-style:none;margin-top:9px}
.checks li{display:flex;align-items:center;gap:9px;height:31px;color:#444}
.checks svg{flex:none}
.closing{margin-top:15px}
.footer{position:absolute;left:0;top:956px;width:1200px;height:107px;background:linear-gradient(#aaa,#4a4a4a)}
.footer-nav{position:absolute;left:174px;top:30px;display:flex;gap:12px;font-size:15px;color:#fff}
.copyright{position:absolute;left:174px;top:54px;font-size:15px;color:var(--lime)}
.contact-bottom{top:28px}
</style>
</head>
<body>
<div class="top-band"></div>

<div class="contact contact-top">
  <svg width="14" height="10" viewBox="0 0 14 10"><rect x=".5" y=".5" width="13" height="9" fill="#fff" stroke="#333"/><path d="M.5 .5 7 6 13.5 .5" fill="none" stroke="#333"/></svg>
  <span>info@maplebeacon.example</span> <span>|</span>
  <svg width="13" height="13" viewBox="0 0 24 24"><path d="M6.6 10.8a15 15 0 0 0 6.6 6.6l2.2-2.2a1 1 0 0 1 1-.25 11 11 0 0 0 3.6.6 1 1 0 0 1 1 1V20a1 1 0 0 1-1 1A17 17 0 0 1 3 4a1 1 0 0 1 1-1h3.5a1 1 0 0 1 1 1 11 11 0 0 0 .6 3.6 1 1 0 0 1-.25 1z" fill="#222"/></svg>
  <span class="phone">587-555-0142</span>
</div>

<div class="frame">
  <aside class="sidebar">
    <div class="brand">
      <div class="brand-name"><i></i>Maple Beacon</div>
      <div class="tagline">Bright Ideas, Steady Growth</div>
    </div>
    <ul class="nav">
      <li>STRATEGY</li><li>PORTFOLIO</li><li>ABOUT US</li><li>CONTACT US</li><li>BLOG</li>
    </ul>
    <div class="connect">
      <span>CONNECT<br>WITH US</span>
      <b><svg width="16" height="14" viewBox="0 0 16 14"><path d="M2 2l5 5-5 5M8 2l5 5-5 5" fill="none" stroke="#fff" stroke-width="2.5"/></svg></b>
    </div>
  </aside>
  <div class="hero" role="img" aria-label="Rows of grey houses with one green house standing out"></div>
  <nav class="tabs">
    <div class="tab">MAPLE BEACON</div>
    <div class="tab">BE FOUND</div>
    <div class="tab">CONNECT</div>
    <div class="tab">GET GROWING</div>
  </nav>
</div>

<div class="social" aria-label="Social links">
  <span></span><span></span><span></span><span></span>
</div>
<div class="tips"><strong>GET TIPS AND TRICKS!</strong><small>Subscribe to our Newsletter.</small></div>
<div class="email-input">your email id</div>
<div class="btn btn-subscribe">Subscribe</div>
<div class="btn btn-quote">Get a Free Quote!</div>
<div class="rule"></div>

<main class="content">
  <h1>WELCOME TO MAPLE BEACON</h1>
  <p>Lorem ipsum dolor sit amet, consectetur adipiscing elit. Morbi dignissim adipiscing turpis et pulvinar. Nulla a sollicitudin libero. Donec euismod iaculis nibh, quis porttitor tellus tempus et. Phasellus viverra arcu eget nisi lacinia consectetur. Pellentesque habitant morbi tristique senectus et netus et malesuada fames ac turpis egestas. Curabitur dignissim ante at libero bibendum nec iaculis lectus sollicitudin. Suspendisse potenti.</p>
  <h2>Our Mission</h2>
  <p>Etiam adipiscing mollis nulla, ac bibendum elit commodo ac. Pellentesque vehicula sodales vulputate. Suspendisse vel semper tortor. Duis tristique pharetra ligula sed bibendum. Etiam adipiscing mollis nulla, ac bibendum elit commodo ac. Etiam adipiscing mollis nulla, ac bibendum elit commodo ac.</p>
  <ul class="checks">
    <li><svg width="18" height="18" viewBox="0 0 18 18"><rect width="18" height="18" rx="3" fill="#8cc63f"/><path d="M4.5 9.5l3 3 6-6.5" fill="none" stroke="#fff" stroke-width="2.2"/></svg>Nam ac risus metus, sit amet blandit ante.</li>
    <li><svg width="18" height="18" viewBox="0 0 18 18"><rect width="18" height="18" rx="3" fill="#8cc63f"/><path d="M4.5 9.5l3 3 6-6.5" fill="none" stroke="#fff" stroke-width="2.2"/></svg>Nunc adipiscing, ipsum eu scelerisque euismod, diam nisl condimentum neque,</li>
    <li><svg width="18" height="18" viewBox="0 0 18 18"><rect width="18" height="18" rx="3" fill="#8cc63f"/><path d="M4.5 9.5l3 3 6-6.5" fill="none" stroke="#fff" stroke-width="2.2"/></svg>Vel gravida ligula velit vitae nisl. Pellentesque at dignissim ipsum. Vivamus id massa arcu.</li>
    <li><svg width="18" height="18" viewBox="0 0 18 18"><rect width="18" height="18" rx="3" fill="#8cc63f"/><path d="M4.5 9.5l3 3 6-6.5" fill="none" stroke="#fff" stroke-width="2.2"/></svg>Phasellus feugiat condimentum neque ac bibendum.</li>
    <li><svg width="18" height="18" viewBox="0 0 18 18"><rect width="18" height="18" rx="3" fill="#8cc63f"/><path d="M4.5 9.5l3 3 6-6.5" fill="none" stroke="#fff" stroke-width="2.2"/></svg>Pellentesque dictum lectus sapien, eu pulvinar eros.</li>
  </ul>
  <p class="closing">Maecenas lacinia, nulla at interdum dapibus, velit sapien posuere eros, et hendrerit purus erat quis est. Proin commodo blandit mauris sed convallis. Donec tellus metus, feugiat sed condimentum congue, dignissim ut leo.</p>
</main>

<footer class="footer">
  <nav class="footer-nav"><span>Site Map</span><span>Strategy</span><span>Portfolio</span><span>About Us</span><span>Contact Us</span><span>Blog</span></nav>
  <div class="copyright">©MAPLE BEACON INC. 2013</div>
  <div class="contact contact-bottom">
    <svg width="14" height="10" viewBox="0 0 14 10"><rect x=".5" y=".5" width="13" height="9" fill="#fff" stroke="#333"/><path d="M.5 .5 7 6 13.5 .5" fill="none" stroke="#333"/></svg>
    <span>info@maplebeacon.example</span> <span>|</span>
    <svg width="13" height="13" viewBox="0 0 24 24"><path d="M6.6 10.8a15 15 0 0 0 6.6 6.6l2.2-2.2a1 1 0 0 1 1-.25 11 11 0 0 0 3.6.6 1 1 0 0 1 1 1V20a1 1 0 0 1-1 1A17 17 0 0 1 3 4a1 1 0 0 1 1-1h3.5a1 1 0 0 1 1 1 11 11 0 0 0 .6 3.6 1 1 0 0 1-.25 1z" fill="#222"/></svg>
    <span class="phone">587-555-0142</span>
  </div>
</footer>
</body>
</html>
```